Brightway Carpet and Tile cleaning Business card Design

I need a design that has the same feel as my van.
i would also like a prominent "Review us on facebook" somewhere, but not that it makes it look silly.
I would like the card to have a little bit of grey or black in the design as well.

It will need contact details
phone: 0455 817264
email: rkbrightwayclean@mailbox-example.com
website: www.brightwaycarpetandtilecleaning-example.com.au
facebook: /brightwaycarpetandtilecleaning

Industry/Entity Type

Business

Contact Information for Business Card

Phone number 0455817264
Email rkbrightwayclean@mailbox-example.com
Website www.brightwaycarpetandtilecleaning-example.com.au
Chatterbox/brightwaycarpetandtilecleaning

Colors
000000

Requirements
Must have
• Same feel as my van
• I want the card to stand out from the crowd
Nice to have
• Maybe include a tiny bit of a third colour? Grey's,blacks, orange?

```html
<!DOCTYPE html>
<html lang="en">
<head>
<meta charset="utf-8">
<title>Brightway Carpet and Tile cleaning – Business Card</title>
<link href="https://fonts.googleapis.com/css2?family=Arimo:wght@400;700&display=swap" rel="stylesheet">
<style>
  :root {
    --stage: #2b2b2c;
    --card: #ffffff;
    --brand-blue: #1aa7d8;
    --brand-dark: #3a3b3e;
    --ink: #2c2c2e;
    --accent-orange: #f07a1a;
    --on-dark: #ffffff;
  }
  * { margin: 0; padding: 0; box-sizing: border-box; }
  html, body {
    width: 1200px; height: 900px; overflow: hidden;
    background: var(--stage);
    font-family: "Arimo", Arial, sans-serif;
  }
  .canvas { position: relative; width: 1200px; height: 900px; }
  .card {
    position: absolute; left: 250px; width: 700px; height: 400px;
    background: var(--card); border-radius: 24px; overflow: hidden;
    box-shadow: 0 10px 30px rgba(0,0,0,.45);
  }
  .card--front { top: 35px; }
  .card--back { top: 465px; }

  .brand {
    position: absolute; display: flex; align-items: center; gap: 12px;
    color: var(--brand-blue); font-weight: 700; font-size: 28px; white-space: nowrap;
  }
  .brand__dot { width: 22px; height: 22px; border-radius: 50%; background: var(--brand-blue); flex: none; }
  .card--front .brand { left: 50%; top: 140px; transform: translateX(-50%); }
  .card--back .brand { left: 50%; top: 70px; transform: translateX(-50%); font-size: 26px; }

  .review {
    position: absolute; left: 0; right: 0; top: 300px;
    display: flex; align-items: center; gap: 14px;
  }
  .review__rule { flex: 1; height: 2px; background: var(--brand-blue); }
  .review__text {
    font-weight: 700; font-size: 19px; letter-spacing: 3px; color: var(--ink); white-space: nowrap;
  }
  .card--front .edge-line {
    position: absolute; left: 0; right: 0; bottom: 28px; height: 3px; background: var(--brand-blue);
  }

  .wave { position: absolute; inset: 0; width: 700px; height: 400px; }
  .holder-name {
    position: absolute; left: 400px; top: 140px;
    color: var(--accent-orange); font-weight: 700; font-size: 26px; letter-spacing: 1px;
  }
  .contacts {
    position: absolute; left: 34px; bottom: 22px; list-style: none;
    color: var(--on-dark); font-size: 15px; line-height: 22px;
  }
  .contacts li { display: flex; align-items: center; gap: 10px; }
  .contacts svg { width: 14px; height: 14px; flex: none; fill: none; stroke: var(--brand-blue); stroke-width: 2; }
</style>
</head>
<body>
<main class="canvas">

  <section class="card card--front" aria-label="Card front">
    <div class="brand"><span class="brand__dot"></span>Brightway Carpet and Tile cleaning</div>
    <div class="review">
      <span class="review__rule"></span>
      <span class="review__text">REVIEW US ON CHATTERBOX</span>
      <span class="review__rule"></span>
    </div>
    <span class="edge-line"></span>
  </section>

  <section class="card card--back" aria-label="Card back">
    <svg class="wave" viewBox="0 0 700 400" aria-hidden="true">
      <path fill="var(--brand-blue)" d="M0,215 C180,255 400,255 500,195 C585,140 610,75 700,65 L700,400 L0,400 Z"/>
      <path fill="var(--brand-dark)" d="M0,232 C185,272 410,272 512,210 C596,155 622,92 700,82 L700,400 L0,400 Z"/>
    </svg>
    <div class="brand"><span class="brand__dot"></span>Brightway Carpet and Tile cleaning</div>
    <p class="holder-name">RYAN</p>
    <ul class="contacts">
      <li><svg viewBox="0 0 16 16"><path d="M3 2h3l1.5 3.5-2 1.2a8 8 0 0 0 3.8 3.8l1.2-2L14 10v3a1 1 0 0 1-1 1A11 11 0 0 1 2 3a1 1 0 0 1 1-1z"/></svg>0455817264</li>
      <li><svg viewBox="0 0 16 16"><rect x="1.5" y="3.5" width="13" height="9"/><path d="M1.5 3.5 8 9l6.5-5.5"/></svg>rkbrightwayclean@mailbox-example.com</li>
      <li><svg viewBox="0 0 16 16"><circle cx="8" cy="8" r="6.5"/><path d="M1.5 8h13M8 1.5c-3 3.5-3 9.5 0 13M8 1.5c3 3.5 3 9.5 0 13"/></svg>www.brightwaycarpetandtilecleaning-example.com.au</li>
      <li><svg viewBox="0 0 16 16"><path d="M2 3h12v8H7l-3 3v-3H2z"/></svg>Chatterbox/brightwaycarpetandtilecleaning</li>
    </ul>
  </section>

</main>
</body>
</html>
```